Financial Planning business needs a Web Design

Web design needed for financial planning business that encompasses investments, insurance and corporate planning. Would like a sleek, simple design that includes elements of nature/trees and lifestyle based imagery, with an overall feel of trustworthiness, security, growth and freedom. We like the layout of www.quellmarkroanefinancial.example, torvinfinancial.example and plomtavery.example, but with more color and images consistent with the nature/lifestyle theme.

Target Market(s)

New and existing clients

Industry/Entity Type

Financial

Number of Pages Required

5+ page

Requirements
Nice to have
• link to twitter feed
• 'latest features' link to articles
• links to action - buy insurance, get a quote, etc/

```html
<!DOCTYPE html>
<html lang="en">
<head>
<meta charset="utf-8">
<title>Keldwick Wealth Planning</title>
<link href="https://fonts.googleapis.com/css2?family=Raleway:wght@500;600&family=Roboto:wght@400;500&display=swap" rel="stylesheet">
<style>
:root{
  --green:#5db321;
  --green-dark:#0d5a2c;
  --nav-grey:#5f6367;
  --text:#555a5e;
  --heading:#2e3134;
  --footer:#111111;
  --footer-base:#0a0a0a;
  --footer-text:#c9c9c9;
  --line:#d9d9d9;
  --white:#ffffff;
}
*{margin:0;padding:0;box-sizing:border-box}
html,body{width:956px;height:1200px;overflow:hidden;background:var(--white)}
body{position:relative;font-family:'Roboto',Arial,sans-serif;color:var(--text)}
.abs{position:absolute}

/* header */
.brand{left:88px;top:20px;display:flex;align-items:center;gap:8px;color:var(--green-dark);font-family:'Raleway',sans-serif;font-weight:600}
.brand-mark{width:40px;height:40px;background:var(--green)}
.brand-name{font-size:17px;line-height:18px}
.brand-sub{font-size:7px;letter-spacing:1.6px;line-height:10px}
.search{left:728px;top:30px;width:139px;height:32px;background:#e6e6e6;font-size:9.5px;color:#8a8a8a;padding:11px 12px}
.search svg{position:absolute;right:11px;top:11px}

/* nav */
.nav{left:0;top:89px;width:956px;height:48px;background:var(--nav-grey);border-top:1px solid #8a8d90}
.nav a{position:absolute;top:18px;color:var(--white);font-size:10px;text-decoration:none}
.nav .active{left:89px;top:9px;width:59px;height:31px;background:var(--green);text-align:center;line-height:31px;border-radius:2px}
.nav .call{right:89px;color:var(--white);font-size:10px;top:18px;position:absolute}

/* hero */
.hero{left:0;top:137px;width:956px;height:448px;background:linear-gradient(100deg,#2e6f8c 0%,#4d8aa1 40%,#8fb3c2 60%,#c9a488 78%,#b9c7cf 100%)}
.hero-ground{left:0;top:520px;width:956px;height:65px;background:linear-gradient(180deg,rgba(180,170,60,.0),#8a8a2a 60%,#5b5a1c)}
.hero-panel{left:0;top:335px;width:468px;height:157px;background:rgba(34,128,110,.78)}
.hero-title{left:87px;top:353px;font-family:'Raleway',sans-serif;font-weight:500;font-size:26px;color:var(--white)}
.hero-text{left:89px;top:389px;width:360px;font-size:9.5px;line-height:16.5px;color:#e9f5f1}
.btn{height:36px;line-height:36px;text-align:center;color:var(--white);font-size:9.5px;border-radius:2px}
.btn-buy{left:89px;top:436px;width:106px;background:var(--green-dark)}
.btn-quote{left:205px;top:436px;width:106px;background:var(--green)}
.dots{left:456px;top:557px;display:flex;gap:7px}
.dots span{width:10px;height:10px;border:1.5px solid var(--white);border-radius:50%}

/* welcome */
.welcome-title{left:0;top:614px;width:956px;text-align:center;font-family:'Raleway',sans-serif;font-weight:500;font-size:17.5px;color:var(--heading)}
.welcome-text{left:90px;top:649px;width:776px;text-align:center;font-size:9.6px;line-height:20.5px}

/* news */
.section-title{font-family:'Raleway',sans-serif;font-weight:500;font-size:17px;color:var(--heading)}
.news-title{left:88px;top:730px}
.news-item{left:88px;width:578px;height:120px;border-bottom:1px solid var(--line)}
.news-thumb{position:absolute;left:1px;top:0;width:133px;height:89px;border-bottom:3px solid var(--green)}
.thumb-office{background:linear-gradient(135deg,#6b6f73,#cfd2d3 55%,#eceeee)}
.thumb-couple{background:linear-gradient(135deg,#b9c6cf,#d9c2a8 55%,#d8cf7a)}
.news-body{position:absolute;left:147px;top:0;width:431px}
.news-head{font-size:10.5px;line-height:16.5px;color:#404448}
.news-date{margin-top:6px;font-size:9.5px;font-weight:500;color:var(--green-dark)}
.news-desc{margin-top:6px;font-size:8.6px;line-height:16.5px;color:#7a7e82}

/* tweets */
.tweets{left:688px;top:734px;width:179px;height:255px;background:var(--green-dark);border-radius:2px;padding:16px 15px 0}
.tweets .section-title{color:var(--white)}
.tweets-rule{margin-top:6px;border-top:1px solid rgba(255,255,255,.15)}
.tweet{position:relative;padding:12px 0 9px 20px;border-bottom:1px solid rgba(255,255,255,.12);font-family:Arial,Helvetica,sans-serif;font-weight:400;font-size:8px;line-height:12px;color:var(--white);height:66px}
.tweet:last-child{border-bottom:0}
.tweet-dot{position:absolute;left:0;top:14px;width:13px;height:13px;border-radius:50%;background:var(--white)}
.tweet-link{color:#8fd45a}
.tweet-time{font-style:italic;color:#9fc7ad}

/* footer */
.footer{left:0;top:1027px;width:956px;height:116px;background:var(--footer)}
.footer-base{left:0;top:1143px;width:956px;height:57px;background:var(--footer-base)}
.footer-title{font-family:'Raleway',sans-serif;font-weight:500;font-size:13px;color:var(--white)}
.footer-text{font-size:9px;line-height:15.5px;color:var(--footer-text)}
.f-contact{left:90px;top:1049px}
.f-news{left:421px;top:1049px}
.f-connect{left:688px;top:1049px}
.f-address{left:90px;top:1075px;padding-left:13px}
.f-mail{left:259px;top:1077px;padding-left:20px}
.f-phone{left:259px;top:1098px;padding-left:20px}
.f-icon{position:absolute;left:0;top:2px}
.email-field{left:422px;top:1079px;width:155px;height:33px;background:var(--white);font-size:8.5px;color:#a8a8a8;padding:11px 11px}
.subscribe{left:577px;top:1079px;width:91px;height:33px;background:var(--green-dark);color:var(--white);font-size:10px;text-align:center;line-height:33px}
.social{left:688px;top:1079px;display:flex;gap:7px}
.social span{width:30px;height:30px;display:block}
.base-links{left:89px;top:1166px;font-size:8.5px;color:var(--footer-text);word-spacing:2px}
.copyright{right:89px;top:1166px;font-size:8.5px;color:#9a9a9a}
.copyright b{font-weight:400;color:var(--footer-text)}
</style>
</head>
<body>

<header>
  <div class="abs brand">
    <span class="brand-mark"></span>
    <div><div class="brand-name">Keldwick</div><div class="brand-sub">WEALTH PLANNING</div></div>
  </div>
  <div class="abs search">Search...
    <svg width="10" height="10" viewBox="0 0 10 10"><circle cx="4" cy="4" r="3" fill="none" stroke="#888" stroke-width="1.4"/><line x1="6.3" y1="6.3" x2="9" y2="9" stroke="#888" stroke-width="1.5"/></svg>
  </div>
</header>

<nav class="abs nav">
  <a class="active" href="#">Home</a>
  <a style="left:176px" href="#">What We Do</a>
  <a style="left:273px" href="#">Articles</a>
  <a style="left:351px" href="#">Team</a>
  <a style="left:421px" href="#">Support</a>
  <a style="left:500px" href="#">Contact</a>
  <span class="call">Call Us : 555 010 4821 00</span>
</nav>

<section>
  <div class="abs hero" role="img" aria-label="Photo of a smiling older couple embracing outdoors under a blue sky"></div>
  <div class="abs hero-ground" aria-hidden="true"></div>
  <div class="abs hero-panel"></div>
  <h1 class="abs hero-title">Financial Planning</h1>
  <p class="abs hero-text">Ut wisi enim ad minim veniam, quis nostrud exerci tation ullamcorper suscipit lobortis nisl ut aliquip ex ea commodo consequat.</p>
  <a class="abs btn btn-buy">Buy Insurance</a>
  <a class="abs btn btn-quote">Get a Quote</a>
  <div class="abs dots"><span></span><span></span><span></span></div>
</section>

<section>
  <h2 class="abs welcome-title">Welcome To Keldwick Wealth Planning</h2>
  <p class="abs welcome-text">Lorem ipsum dolor sit amet, consectetuer adipiscing elit, sed diam nonummy nibh euismod tincidunt ut laoreet dolore magna aliquam erat volutpat. Ut wisi enim ad minim veniam, quis nostrud exerci tation ullamcorper suscipit lobortis nisl ut aliquip ex ea commodo consequat. Duis autem vel eum iriure dolor in hendrerit in vulputate velit esse molestie cons equat, vel illum dolore eu feugiat nulla facilisis at vero eros et accumsan et iusto odio dignissim qui blandit.</p>
</section>

<section>
  <h2 class="abs section-title news-title">Latest News</h2>
  <article class="abs news-item" style="top:767px;height:107px">
    <div class="news-thumb thumb-office" role="img" aria-label="Photo of a woman working with a calculator at a desk"></div>
    <div class="news-body">
      <p class="news-head">Lorem ipsum dolor sit amet, consectetuer adipiscing elit, sed diam nonummy nibh euismod tincidunt ut laoreet dolore magna aliquam erat volutpat</p>
      <p class="news-date">May 12, 2015</p>
      <p class="news-desc">Ut wisi enim ad minim veniam, quis nostrud exerci tation ullamcorper suscipit lobortis nisl ut aliquip ex ea commodo consequat...</p>
    </div>
  </article>
  <article class="abs news-item" style="top:886px;height:108px">
    <div class="news-thumb thumb-couple" role="img" aria-label="Photo of an older couple smiling in a field"></div>
    <div class="news-body">
      <p class="news-head">Duis autem vel eum iriure dolor in hendrerit in vulputate velit esse molestie consequat, vel illum dolore eu feugiat nulla facilisis at vero eros et accumsan et iusto</p>
      <p class="news-date">May 11, 2015</p>
      <p class="news-desc">Ut wisi enim ad minim veniam, quis nostrud exerci tation ullamcorper suscipit lobortis nisl ut aliquip ex ea commodo consequat...</p>
    </div>
  </article>

  <aside class="abs tweets">
    <h2 class="section-title">Latest Tweets</h2>
    <div class="tweets-rule"></div>
    <div class="tweet"><span class="tweet-dot"></span>Lorem ipsum dolor sit amet, conse adipiscing elit, sed diam nonu<br><span class="tweet-link">http://lnk.example/trg87z</span><br><span class="tweet-time">24 minutes ago</span></div>
    <div class="tweet"><span class="tweet-dot"></span>Ut wisi enim ad minim veniam, quis nostrud exerci<br><span class="tweet-link">http://lnk.example/trg87z</span><br><span class="tweet-time">24 minutes ago</span></div>
    <div class="tweet"><span class="tweet-dot"></span>Eodem modo typi, qui nunc nobis videntur parum clari<br><span class="tweet-link">http://lnk.example/trg87z</span><br><span class="tweet-time">24 minutes ago</span></div>
  </aside>
</section>

<footer>
  <div class="abs footer"></div>
  <h3 class="abs footer-title f-contact">Contact us</h3>
  <div class="abs footer-text f-address">
    <svg class="f-icon" style="top:2px" width="8" height="11" viewBox="0 0 8 11"><path d="M4 0a4 4 0 0 1 4 4c0 3-4 7-4 7S0 7 0 4a4 4 0 0 1 4-4z" fill="#5db321"/><circle cx="4" cy="4" r="1.5" fill="#111"/></svg>
    Keldwick Wealth Planning<br>P.O. Box 982, Fernwell Rd,<br>Ashmoor 60314
  </div>
  <div class="abs footer-text f-mail">
    <svg class="f-icon" width="13" height="10" viewBox="0 0 13 10"><rect width="13" height="10" rx="1" fill="#5db321"/><path d="M0 1l6.5 5L13 1" fill="none" stroke="#111" stroke-width="1.2"/></svg>
    hello@keldwickwealth.example
  </div>
  <div class="abs footer-text f-phone">
    <svg class="f-icon" width="12" height="12" viewBox="0 0 12 12"><rect width="12" height="12" rx="2" fill="#5db321"/><path d="M3.5 2.5l1.5 2-1 1c.6 1.2 1.3 1.9 2.5 2.5l1-1 2 1.5-1 1.5C5.5 9.8 2.2 6.5 2 3.5z" fill="#111"/></svg>
    +555.010.482.1000
  </div>

  <h3 class="abs footer-title f-news">Newsletter SIgnup</h3>
  <div class="abs email-field">Email Address</div>
  <div class="abs subscribe">Subscribe</div>

  <h3 class="abs footer-title f-connect">Connect Us</h3>
  <div class="abs social">
    <span style="background:#3a5795" role="img" aria-label="Social network link"></span>
    <span style="background:#2fa8dc" role="img" aria-label="Social network link"></span>
    <span style="background:#b9191c" role="img" aria-label="Video channel link"></span>
    <span style="background:#cf3a2a" role="img" aria-label="Social network link"></span>
    <span style="background:#f06721" role="img" aria-label="News feed link"></span>
  </div>

  <div class="abs footer-base"></div>
  <div class="abs base-links">About us &nbsp;| &nbsp;FAQ &nbsp;| &nbsp;Services</div>
  <div class="abs copyright">Copyright &nbsp;@ 2015 <b>Keldwick Wealth Planning</b>. All Right Reserved.</div>
</footer>

</body>
</html>
```